Road Construction Company needs business cards

We would like a new business card designed for our business.

We're a road construction company based in Qld, Australia.

Can the business card please have the following information on it.

Name: Warren Halbeck
Position: General Manager
Phone: 0472 915 348
Email: Warren.halbeck@tovrin.com.au
Address: 87 Marrow Ave, Pendlebay, QLD, 4023
Website: www.tovrin.com.au

Visually we'd like the card to be professional and simple.

Attached is our logo.

Our website is www.tovrin.com.au

Target Market(s)

Men aged 25-60

Contact Information for Business Card

As listed in project description

Font styles to use
Serif

Requirements
Must have
• Large logo on back of card

```html
<!DOCTYPE html>
<html lang="en">
<head>
<meta charset="utf-8">
<title>Tovrin business card</title>
<link href="https://fonts.googleapis.com/css2?family=Open+Sans:wght@400;600;800&display=swap" rel="stylesheet">
<style>
  :root {
    --stage: #4b4b4b;
    --brand-blue: #1456a4;
    --accent-blue: #3ea6dc;
    --ink: #111111;
    --paper: #ffffff;
  }
  * { margin: 0; padding: 0; box-sizing: border-box; }
  html, body {
    width: 1200px; height: 780px; overflow: hidden;
    background: var(--stage);
    font-family: "Open Sans", Arial, sans-serif;
  }
  .stage {
    width: 1200px; height: 780px;
    display: flex; align-items: center; justify-content: center; gap: 40px;
  }
  .card {
    width: 540px; height: 330px;
    position: relative;
    box-shadow: 0 6px 18px rgba(0,0,0,0.35);
  }
  .card-back {
    background: var(--brand-blue);
    display: flex; align-items: center; justify-content: center;
  }
  .card-back .wordmark {
    color: var(--paper);
    font-weight: 800;
    font-size: 92px;
    letter-spacing: 2px;
    text-transform: uppercase;
  }
  .card-front { background: var(--paper); }
  .card-front .wordmark {
    position: absolute;
    left: 0; width: 290px; top: 140px;
    text-align: center;
    color: var(--brand-blue);
    font-weight: 800;
    font-size: 46px;
    letter-spacing: 1px;
    text-transform: uppercase;
  }
  .divider {
    position: absolute;
    left: 290px; top: 60px;
    width: 1px; height: 210px;
    background: var(--ink);
  }
  .contact-block {
    position: absolute;
    left: 308px; top: 66px; right: 14px;
    color: var(--ink);
  }
  .person-name {
    color: var(--brand-blue);
    font-weight: 800;
    font-size: 25px;
    line-height: 1.1;
  }
  .person-role {
    font-weight: 600;
    font-size: 14px;
    margin-top: 2px;
  }
  .address {
    font-size: 13.5px;
    line-height: 1.3;
    margin-top: 14px;
  }
  .contact-list {
    list-style: none;
    margin-top: 14px;
    font-size: 13px;
    line-height: 1.5;
  }
  .contact-list li {
    display: flex; align-items: center; gap: 8px;
    white-space: nowrap;
  }
  .contact-list svg { width: 13px; height: 13px; flex: none; }
  .icon-stroke { fill: none; stroke: var(--accent-blue); stroke-width: 2; stroke-linecap: round; stroke-linejoin: round; }
</style>
</head>
<body>
<main class="stage">
  <section class="card card-back" aria-label="Back of card">
    <span class="wordmark">Tovrin</span>
  </section>

  <section class="card card-front" aria-label="Front of card">
    <span class="wordmark">Tovrin</span>
    <div class="divider"></div>
    <div class="contact-block">
      <h1 class="person-name">Warren Halbeck</h1>
      <p class="person-role">General Manager</p>
      <p class="address">87 Marrow Ave,<br>Pendlebay, QLD, 4023</p>
      <ul class="contact-list">
        <li>
          <svg viewBox="0 0 24 24" aria-hidden="true"><path class="icon-stroke" d="M5 3h4l2 5-2.5 1.5a11 11 0 0 0 6 6L16 13l5 2v4a2 2 0 0 1-2 2A17 17 0 0 1 3 5a2 2 0 0 1 2-2z"/></svg>
          0472 915 348
        </li>
        <li>
          <svg viewBox="0 0 24 24" aria-hidden="true"><circle class="icon-stroke" cx="12" cy="12" r="9"/><path class="icon-stroke" d="M3 12h18M12 3a14 14 0 0 1 0 18M12 3a14 14 0 0 0 0 18"/></svg>
          www.tovrin.com.au
        </li>
        <li>
          <svg viewBox="0 0 24 24" aria-hidden="true"><rect class="icon-stroke" x="3" y="5" width="18" height="14" rx="1"/><path class="icon-stroke" d="M3 6l9 7 9-7"/></svg>
          Warren.halbeck@tovrin.com.au
        </li>
      </ul>
    </div>
  </section>
</main>
</body>
</html>
```